Black Matte card with samurai logo which I would like it to be textured and company name on one side and on the other side I would like the company information with the reno (Face logo) Sushi logo. Double Sided card.

majority customers are University students, University sororities and fraternities.

It Company

Reno Sushi
317 W. Harlow Ave
Tucson, AZ 85042
Phone (520)413-6271
Fax (520)357-1846
E-mail: Renosushidesert@mailbox-example.com
FB: Renosushidesert
Twitter: Renosushidesert

• Present Normal

```html
<!DOCTYPE html>
<html lang="en">
<head>
<meta charset="utf-8">
<title>Reno Sushi – Business Card</title>
<link rel="stylesheet" href="https://fonts.googleapis.com/css2?family=PT+Sans:wght@400;700&display=swap">
<style>
  :root {
    --stage: #a9845b;
    --card-dark: #1b1b1b;
    --card-mid: #2e2e2e;
    --card-light: #3a3a3a;
    --ink: #f2f2f2;
    --brand-red: #c8312b;
    --band-red: #b3282a;
    --silver-hi: #f4f4f4;
    --silver-lo: #a9a9a9;
    --social-ink: #3b3b3b;
    --divider: rgba(255,255,255,0.55);
  }
  * { box-sizing: border-box; margin: 0; padding: 0; }
  html, body {
    width: 1200px; height: 744px; overflow: hidden;
    background: var(--stage);
    font-family: "PT Sans", Arial, sans-serif;
  }
  .sheet { position: relative; width: 1200px; height: 744px; }

  .card {
    position: absolute;
    width: 562px; height: 320px;
    border-radius: 20px;
    overflow: hidden;
    background: linear-gradient(180deg, var(--card-mid) 0%, var(--card-dark) 45%, var(--card-light) 75%, var(--card-dark) 100%);
    box-shadow: 0 3px 8px rgba(0,0,0,0.35);
  }
  .card-front { left: 346px; top: 26px; }
  .card-back-1 { left: 20px; top: 368px; }
  .card-back-2 { left: 616px; top: 368px; }

  .texture {
    position: absolute; inset: 0;
    background: linear-gradient(90deg, rgba(255,255,255,0.04), rgba(0,0,0,0.15) 50%, rgba(255,255,255,0.04));
  }

  /* Front */
  .front-name {
    position: absolute; left: 20px; top: 118px; width: 220px;
    text-align: center;
    color: var(--brand-red);
    font-size: 34px; font-weight: 400; line-height: 1.05;
  }
  .divider {
    position: absolute; left: 248px; top: 81px;
    width: 1px; height: 116px; background: var(--divider);
  }
  .contact {
    position: absolute; left: 266px; top: 86px;
    color: var(--ink); font-size: 13.5px; line-height: 1;
    list-style: none;
  }
  .contact li { display: flex; align-items: center; height: 21.5px; }
  .contact svg { width: 13px; height: 13px; margin-right: 7px; flex: none; }
  .address {
    position: absolute; left: 266px; top: 159px;
    color: var(--ink); font-size: 13.5px; line-height: 20px;
    font-style: normal;
  }
  .swoosh { position: absolute; left: 0; bottom: 0; width: 562px; height: 90px; }
  .social {
    position: absolute; left: 371px; top: 276px;
    list-style: none; color: var(--social-ink); font-size: 13.5px;
  }
  .social li { display: flex; align-items: center; height: 24px; }
  .social-square {
    width: 16px; height: 16px; background: var(--band-red);
    margin-right: 6px; border-radius: 2px;
  }

  /* Backs */
  .back-name {
    position: absolute; inset: 0;
    display: flex; align-items: center; justify-content: center; gap: 18px;
    color: var(--brand-red);
    font-size: 58px; font-weight: 400;
  }
  .back-dot {
    width: 34px; height: 34px; border-radius: 50%;
    background: var(--brand-red);
  }

  .label {
    position: absolute; top: 694px;
    color: #fff; font-size: 22px; font-weight: 400;
  }
  .label-1 { left: 244px; }
  .label-2 { left: 841px; }
</style>
</head>
<body>
<main class="sheet">

  <section class="card card-front" aria-label="Card front">
    <div class="texture"></div>
    <div class="front-name">Reno<br>Sushi</div>
    <div class="divider"></div>
    <ul class="contact">
      <li>
        <svg viewBox="0 0 16 16" aria-hidden="true"><path fill="#f2f2f2" d="M3 1.5l3 .2 1 3.3-1.8 1.3a8 8 0 0 0 4.5 4.5L11 9l3.3 1 .2 3-2 2C6 15 1 10 1 3.5z"/></svg>
        (520)413-6271
      </li>
      <li>
        <svg viewBox="0 0 16 16" aria-hidden="true"><rect x="4" y="1" width="8" height="14" rx="1.5" fill="#f2f2f2"/><rect x="5.5" y="3" width="5" height="6" fill="#1b1b1b"/></svg>
        (520)357-1846
      </li>
      <li>
        <svg viewBox="0 0 16 16" aria-hidden="true"><rect x="1" y="3.5" width="14" height="9" rx="1" fill="#f2f2f2"/><path d="M1.5 4l6.5 5 6.5-5" fill="none" stroke="#1b1b1b" stroke-width="1.3"/></svg>
        renosushidesert@mailbox-example.com
      </li>
    </ul>
    <address class="address">317 W. Harlow Ave Tucson<br>AZ 85042</address>
    <svg class="swoosh" viewBox="0 0 562 90" preserveAspectRatio="none" aria-hidden="true">
      <defs>
        <linearGradient id="silver" x1="0" y1="0" x2="1" y2="0">
          <stop offset="0" stop-color="#d8d8d8"/>
          <stop offset="0.5" stop-color="#f4f4f4"/>
          <stop offset="1" stop-color="#b8b8b8"/>
        </linearGradient>
      </defs>
      <path d="M0 42 C 140 20, 330 18, 562 16 L562 90 L0 90 Z" fill="#9a9a9a"/>
      <path d="M0 47 C 150 28, 340 24, 562 22 L562 90 L0 90 Z" fill="url(#silver)"/>
      <path d="M0 58 C 120 60, 250 50, 340 30 C 260 62, 150 78, 0 78 Z" fill="var(--band-red)"/>
      <path d="M0 78 C 150 78, 260 62, 340 30 C 300 70, 220 90, 160 90 L0 90 Z" fill="#d0d0d0"/>
    </svg>
    <ul class="social">
      <li><span class="social-square"></span>renosushidesert</li>
      <li><span class="social-square"></span>renosushidesert</li>
    </ul>
  </section>

  <section class="card card-back-1" aria-label="Card back option one">
    <div class="texture"></div>
    <div class="back-name"><span class="back-dot"></span>Reno Sushi</div>
  </section>

  <section class="card card-back-2" aria-label="Card back option two">
    <div class="texture"></div>
    <div class="back-name"><span class="back-dot"></span>Reno Sushi</div>
  </section>

  <p class="label label-1">Back-1</p>
  <p class="label label-2">Back-2</p>

</main>
</body>
</html>
```